BildeVOLD buisnesscard

Hey :) I need a modern buisnesscard for my company BildeVOLD
It most have:
Dagligleder og Fotograf: Henrik Audun Strandvik

Mob: +4791264085
Epost: post@bildevold.example
Adresse: Kvernbakken9, 6040 Fjellvåg

Facbook and instagram logo with text BildeVOLD

BildeVOLD logo

It Company

```html
<!DOCTYPE html>
<html lang="no">
<head>
<meta charset="utf-8">
<title>BildeVOLD – visittkort</title>
<link rel="stylesheet" href="https://fonts.googleapis.com/css2?family=Open+Sans:wght@400;600;700&display=swap">
<style>
  :root {
    --page-bg: #ececec;
    --card-white: #ffffff;
    --brand-pink: #c94886;
    --brand-blue: #2580b3;
    --text-white: #ffffff;
  }
  html, body {
    margin: 0;
    padding: 0;
    width: 1105px;
    height: 1200px;
    overflow: hidden;
    background: var(--page-bg);
    font-family: "Open Sans", Arial, sans-serif;
  }
  .canvas {
    position: relative;
    width: 1105px;
    height: 1200px;
  }
  .card {
    position: absolute;
    left: 192px;
    width: 720px;
    height: 410px;
    overflow: hidden;
  }
  .card--front { top: 167px; background: var(--card-white); }
  .card--back  { top: 623px; background: var(--brand-blue); }

  .card__shapes {
    position: absolute;
    inset: 0;
  }
  .wordmark {
    position: absolute;
    margin: 0;
    font-weight: 700;
    letter-spacing: -0.5px;
    line-height: 1;
  }
  .wordmark--front {
    left: 46px;
    top: 146px;
    font-size: 50px;
    color: var(--brand-blue);
  }
  .wordmark--back {
    left: 0;
    right: 0;
    top: 232px;
    text-align: center;
    font-size: 56px;
    color: var(--text-white);
  }

  .contact {
    position: absolute;
    right: 32px;
    top: 196px;
    text-align: right;
    color: var(--text-white);
  }
  .contact__name {
    margin: 0;
    font-size: 25px;
    font-weight: 600;
    line-height: 1.2;
  }
  .contact__role {
    margin: 3px 0 18px;
    font-size: 19px;
    line-height: 1.2;
  }
  .contact__list {
    list-style: none;
    margin: 0;
    padding: 0;
    font-size: 18px;
    line-height: 28.5px;
  }
  .contact__item {
    display: flex;
    justify-content: flex-end;
    align-items: center;
    gap: 8px;
  }
  .contact__icon {
    width: 18px;
    height: 18px;
    flex: none;
  }

  .social {
    position: absolute;
    left: 0;
    right: 0;
    top: 339px;
    display: flex;
    justify-content: center;
    align-items: center;
    gap: 10px;
    color: var(--text-white);
  }
  .social__rule {
    width: 62px;
    height: 2px;
    background: linear-gradient(90deg, rgba(255,255,255,0), rgba(255,255,255,0.9));
  }
  .social__rule--right {
    background: linear-gradient(90deg, rgba(255,255,255,0.9), rgba(255,255,255,0));
  }
  .social__dot {
    width: 30px;
    height: 30px;
    border: 2px solid var(--text-white);
    border-radius: 50%;
    box-sizing: border-box;
  }
  .social__handle {
    font-size: 16px;
    font-weight: 600;
  }
</style>
</head>
<body>
<main class="canvas">

  <section class="card card--front" aria-label="Visittkort forside">
    <svg class="card__shapes" viewBox="0 0 720 410" width="720" height="410" aria-hidden="true">
      <polygon points="556,0 573,0 193,410 176,410" fill="var(--brand-blue)"/>
      <polygon points="580,0 720,0 720,410 200,410" fill="var(--brand-pink)"/>
    </svg>

    <p class="wordmark wordmark--front">BildeVOLD</p>

    <div class="contact">
      <h1 class="contact__name">Henrik Audun Strandvik</h1>
      <p class="contact__role">Dagligleder og Fotograf</p>
      <ul class="contact__list">
        <li class="contact__item">+4791264085
          <svg class="contact__icon" viewBox="0 0 18 18" aria-hidden="true">
            <rect x="4.5" y="1" width="9" height="16" rx="1.5" fill="none" stroke="#fff" stroke-width="1.6"/>
            <rect x="7" y="14" width="4" height="1.4" fill="#fff"/>
          </svg>
        </li>
        <li class="contact__item">post@bildevold.example
          <svg class="contact__icon" viewBox="0 0 18 18" aria-hidden="true">
            <rect x="1.5" y="4" width="15" height="10" fill="#fff"/>
            <polyline points="1.5,4 9,10 16.5,4" fill="none" stroke="var(--brand-pink)" stroke-width="1.3"/>
          </svg>
        </li>
        <li class="contact__item">www.bildevold.example
          <svg class="contact__icon" viewBox="0 0 18 18" aria-hidden="true">
            <circle cx="9" cy="9" r="7.5" fill="#fff"/>
            <ellipse cx="9" cy="9" rx="3.2" ry="7.5" fill="none" stroke="var(--brand-pink)" stroke-width="1.1"/>
            <line x1="1.5" y1="9" x2="16.5" y2="9" stroke="var(--brand-pink)" stroke-width="1.1"/>
          </svg>
        </li>
        <li class="contact__item">Kvernbakken9, 6040 Fjellvåg</li>
      </ul>
    </div>
  </section>

  <section class="card card--back" aria-label="Visittkort bakside">
    <p class="wordmark wordmark--back">BildeVOLD</p>
    <div class="social">
      <span class="social__rule"></span>
      <span class="social__dot"></span>
      <span class="social__handle">BildeVOLD</span>
      <span class="social__rule social__rule--right"></span>
    </div>
  </section>

</main>
</body>
</html>
```